Vantro cards

I am in the auto motive, transportation business I would like a business card that is Something cool, modern edgy, having to do with car culture. I offer towing service for high and exotic cars. I also provide towing for collisions and car accidents. I offer open and enclosed transport nationwide.

Target Market(s)

Car culture people high end auto collectors

Industry/Entity Type

Towing car carrier

Contact Information for Business Card

My company colors black yellow and silver

Font styles to use
Serif

```html
<!DOCTYPE html>
<html lang="en">
<head>
<meta charset="utf-8">
<title>Vantro Transportation – Business Cards</title>
<link href="https://fonts.googleapis.com/css2?family=Arimo:wght@400;700&display=swap" rel="stylesheet">
<style>
  :root {
    --stage: #2a2a2a;
    --card: #1f1f1f;
    --yellow: #f7dd55;
    --silver: #b4b4b6;
    --white: #f4f4f4;
    --rule: #8a8a8a;
  }
  * { box-sizing: border-box; margin: 0; padding: 0; }
  html, body { width: 1200px; height: 1200px; overflow: hidden; }
  body {
    background: var(--stage);
    font-family: "Arimo", Arial, sans-serif;
    display: flex;
    align-items: center;
    justify-content: center;
    gap: 60px;
  }
  .card {
    width: 400px;
    height: 660px;
    background: var(--card);
    border-radius: 26px;
    box-shadow: 0 18px 40px rgba(0,0,0,.45);
    display: flex;
    flex-direction: column;
    align-items: center;
    color: var(--white);
    text-align: center;
  }
  .card--front { padding-top: 110px; }
  .card--back { justify-content: center; }
  .brand {
    color: var(--yellow);
    font-weight: 700;
    letter-spacing: 2px;
    line-height: 1.15;
  }
  .card--front .brand { font-size: 34px; }
  .card--back .brand { font-size: 40px; }
  .brand__sub { display: block; font-size: .5em; letter-spacing: 4px; }
  .holder { margin-top: 110px; }
  .holder__name { color: var(--yellow); font-weight: 700; font-size: 26px; letter-spacing: 1px; }
  .holder__title { font-size: 18px; margin-top: 2px; }
  .icon-row {
    display: flex; align-items: center; gap: 8px;
    margin-top: 22px; width: 320px;
  }
  .icon-row::before, .icon-row::after {
    content: ""; flex: 1; height: 1px; background: var(--rule);
  }
  .icon { width: 26px; height: 26px; }
  .contact { margin-top: 14px; font-size: 17px; line-height: 1.45; }
  .divider { width: 320px; height: 1px; background: var(--rule); margin: 16px 0 14px; }
  .address { font-size: 17px; line-height: 1.4; }
</style>
</head>
<body>
  <section class="card card--front">
    <div class="brand">VANTRO<span class="brand__sub">TRANSPORTATION</span></div>
    <div class="holder">
      <p class="holder__name">DORIAN WELLER</p>
      <p class="holder__title">CEO/Founder</p>
    </div>
    <div class="icon-row">
      <svg class="icon" viewBox="0 0 26 26" aria-label="phone"><rect width="26" height="26" rx="6" fill="var(--yellow)"/><path d="M8 7c1-1 2-1 3 1l1 2-2 1c1 2 2 3 4 4l1-2 2 1c2 1 2 2 1 3-3 2-11-5-10-10z" fill="var(--card)"/></svg>
      <svg class="icon" viewBox="0 0 26 26" aria-label="mobile"><rect width="26" height="26" rx="6" fill="var(--yellow)"/><rect x="9" y="6" width="8" height="14" rx="1.5" fill="none" stroke="var(--card)" stroke-width="1.8"/></svg>
      <svg class="icon" viewBox="0 0 26 26" aria-label="email"><rect width="26" height="26" rx="6" fill="var(--yellow)"/><rect x="6" y="8" width="14" height="10" fill="var(--card)"/><path d="M6 8l7 6 7-6" fill="none" stroke="var(--yellow)" stroke-width="1.4"/></svg>
      <svg class="icon" viewBox="0 0 26 26" aria-label="website"><rect width="26" height="26" rx="6" fill="var(--yellow)"/><circle cx="13" cy="13" r="6.5" fill="none" stroke="var(--card)" stroke-width="1.6"/><ellipse cx="13" cy="13" rx="2.8" ry="6.5" fill="none" stroke="var(--card)" stroke-width="1.3"/><path d="M6.5 13h13" stroke="var(--card)" stroke-width="1.3"/></svg>
    </div>
    <div class="contact">
      <p>(555) 210 4477</p>
      <p>(555) 318 9062</p>
      <p>info@vantrotransport.com</p>
      <p>www.vantrotransport.com</p>
    </div>
    <div class="divider"></div>
    <div class="address">
      <p>P.O. Box 4870 Street</p>
      <p>Country Name CD 3196</p>
    </div>
  </section>

  <section class="card card--back">
    <div class="brand">VANTRO<span class="brand__sub">TRANSPORTATION</span></div>
  </section>
</body>
</html>
```